Operator Qualification Testing Flyer

I have a 8x10 basic flyer that I created usin InDesign for one of our services our company provides. I would like to see more options for the layout and general design of the flyer. This flyer will be used as a template for the other services we provide. I will include the InDesign Folder with all the logos and images. Please feel free to use any logo design within the folder and you can change the font and/or colors as needed. I would like the final output in a Indesign package folder to be used in InDesign 2021

Target Market(s)

Business to Business marketing in the Oil and Gas industry

Font styles to use
Sans Serif

Colors
85cae6
85acd3
3377b5
0355a3
0792cd
ffffff
cedeed

Requirements
Must have
• I included/attached a couple of brochures styles that I do like.

```html
<!DOCTYPE html>
<html lang="en">
<head>
<meta charset="utf-8">
<title>Pipeline OQ Testing Flyer</title>
<link href="https://fonts.googleapis.com/css2?family=Arimo:wght@700&family=Open+Sans:wght@400;600;700&display=swap" rel="stylesheet">
<style>
  :root {
    --sky: #85cae6;
    --steel: #85acd3;
    --mid-blue: #3377b5;
    --navy: #0355a3;
    --brand-blue: #0792cd;
    --white: #ffffff;
    --mist: #cedeed;
    --backdrop: #c4c4c6;
    --ink: #3c4247;
    --earth-dark: #4a4843;
    --earth-light: #9c917c;
  }
  * { box-sizing: border-box; margin: 0; padding: 0; }
  html, body { width: 1200px; height: 960px; overflow: hidden; }
  body {
    background: var(--backdrop);
    font-family: "Open Sans", Arial, sans-serif;
    position: relative;
  }
  .flyer {
    position: absolute;
    left: 280px; top: 80px;
    width: 640px; height: 800px;
    background: linear-gradient(180deg, var(--white) 45%, #eceef0 100%);
    overflow: hidden;
  }
  .flyer-header { position: absolute; left: 0; top: 0; width: 640px; height: 300px; }
  .brand {
    position: absolute; left: 40px; top: 32px;
    display: flex; align-items: center; gap: 12px;
    color: var(--white); font-size: 21px; font-weight: 400;
  }
  .brand-mark {
    width: 24px; height: 24px; border-radius: 50%;
    background: var(--brand-blue);
  }
  .title {
    position: absolute; left: 40px; top: 228px;
    font-family: "Arimo", Arial, sans-serif; font-weight: 700;
    font-size: 42px; line-height: 1; letter-spacing: 1px; color: var(--white);
  }
  .content { position: absolute; left: 56px; top: 318px; width: 520px; }
  .content h2 {
    color: var(--brand-blue); font-size: 17px; font-weight: 700;
    line-height: 1.3; margin: 0 0 6px;
  }
  .content p {
    color: var(--ink); font-size: 11px; line-height: 1.45;
    margin: 0 0 8px;
  }
  .narrow { width: 380px; }
  .section { margin-bottom: 12px; }
  .warning-sign {
    position: absolute; left: 472px; top: 478px;
    width: 112px; height: 112px; border-radius: 50%;
    background: radial-gradient(circle, #e4a11b 0%, #e4a11b 58%, #2a2a2a 61%, #2a2a2a 100%);
  }
  .contact { position: absolute; left: 452px; top: 612px; width: 150px; }
  .contact-item {
    height: 74px; display: flex; flex-direction: column;
    align-items: center; justify-content: center; gap: 8px;
    color: var(--white); font-size: 11px;
  }
  .contact-phone { background: var(--brand-blue); }
  .contact-email { background: var(--sky); }
  .contact-icon {
    width: 18px; height: 18px; border-radius: 50%;
    background: var(--navy); display: flex; align-items: center; justify-content: center;
  }
</style>
</head>
<body>
<main class="flyer">
  <svg class="flyer-header" viewBox="0 0 640 300" width="640" height="300">
    <defs>
      <linearGradient id="site-tones" x1="0" y1="0" x2="1" y2="1">
        <stop offset="0" stop-color="var(--earth-dark)"/>
        <stop offset="0.55" stop-color="#7a705f"/>
        <stop offset="1" stop-color="var(--earth-light)"/>
      </linearGradient>
    </defs>
    <path d="M0 0 H640 V200 L0 250 Z" fill="url(#site-tones)" role="img" aria-label="Aerial photo of a pipeline construction site with excavator and pipelayer beside a trench"/>
    <path d="M0 206 L600 170 L640 170 L640 186 L0 224 Z" fill="var(--sky)" opacity="0.8"/>
    <path d="M0 218 L600 218 L562 282 L0 282 Z" fill="var(--brand-blue)"/>
    <path d="M562 282 L600 218 L640 218 L640 228 L608 282 Z" fill="var(--mist)" opacity="0.8"/>
  </svg>
  <div class="brand"><span class="brand-mark"></span>Meridian Field Services Inc.</div>
  <h1 class="title">PIPELINE OQ TESTING</h1>

  <section class="content">
    <div class="section">
      <h2>What Is Operator Qualification?</h2>
      <p>Operator Qualifications (OQ) for DOT Oil/Gas Pipelines are requirements set by Department of Transportation (DOT) and Pipeline and Hazardous Materials Safety Administration (PHMSA). To assure safety in the transport of hazardous gases and liquids in the nation's pipelines, pipeline operators who perform covered tasks must be qualified. Qualified means that an individual has been evaluated and can perform assigned covered tasks and recognize and react to abnormal operating conditions.</p>
    </div>
    <div class="section narrow">
      <h2>What Are Covered Tasks?</h2>
      <p>Covered tasks are defined in an operator's written plan which defines specific job functions or activities personnel are qualified to perform on a pipeline facility.</p>
    </div>
    <div class="section narrow">
      <h2>What We Provide</h2>
      <p>Meridian Field Services Inc. utilizes Craftline pipeline program to administer OQ assessment testing on 127 covered tasks</p>
      <p>Upon completion of OQ testing the information is first transferred to Craftline's Registry System and automatically uploaded to TrustGrid.</p>
      <p>In addition to the benefits provided by TrustGrid's database, the Craftline Registry System houses all the completion information allowing candidates to share their training information and employers to verify successful covered task and level completions.</p>
    </div>
  </section>

  <div class="warning-sign" role="img" aria-label="Round petroleum pipeline warning marker sign"></div>

  <aside class="contact">
    <div class="contact-item contact-phone">
      <span class="contact-icon">
        <svg width="10" height="10" viewBox="0 0 24 24"><path fill="#fff" d="M6.6 10.8a15 15 0 0 0 6.6 6.6l2.2-2.2a1 1 0 0 1 1-.25 11.4 11.4 0 0 0 3.6.57 1 1 0 0 1 1 1V20a1 1 0 0 1-1 1A17 17 0 0 1 3 4a1 1 0 0 1 1-1h3.5a1 1 0 0 1 1 1c0 1.25.2 2.45.57 3.57a1 1 0 0 1-.25 1z"/></svg>
      </span>
      406-555-0142
    </div>
    <div class="contact-item contact-email">
      <span class="contact-icon">
        <svg width="10" height="10" viewBox="0 0 24 24"><path fill="#fff" d="M2 5h20v14H2z M2 5l10 8 10-8" stroke="var(--navy)" stroke-width="1.5"/></svg>
      </span>
      info@meridianfield.co
    </div>
  </aside>
</main>
</body>
</html>
```